Create a landing page for a new product market combination for an international software company

We are a software company being in the BtoB market for over 20 years. Our product is a software tool that allows for very flexible and versatile cost calculations for companies. We sell to all industries in over 40 countries with 500 clients. We have fairly recently seen a succesfull "competitor" (www.vorlinex.com) come up in the niche market of IT costing. This competitor has launched an independent platform with regards to managing IT costs (www.QRHguild.org). In this independent platform standards are set, events are organised and books are written. Since our software can handle all type of costing questions we can en already do play a role in IT costing. We have therefore become a sponsor of the QRH guild. Besides that we came accross the opportunity to buy the URL: www.qrhsoftware.com Which we did. We are now looking for a design on that landing page that communicates the fact that the visitor has landed with a company that have in depth knowledge on the QRH subject and provide an effective an affordable tooling for QRH. Currently the difference between the professionalism of our own website (www.pricelumen.com) and that of the competitor (www.vorlinex.com) and the independent council (www.qrhguild.org). is too big.

Target Market(s)

BtB with large IT spend

Number of Pages Required

1 page

Colors

Designer to choose colors to be used in the design.

Requirements
Must have
• A proffessional look and feel
Should not have
• Definetely not too much information and wording

```html
<!DOCTYPE html>
<html lang="en">
<head>
<meta charset="utf-8">
<title>QRH Software</title>
<link href="https://fonts.googleapis.com/css2?family=Lato:wght@300;400;700;900&display=swap" rel="stylesheet">
<style>
:root{
  --blue:#1f7fc4;
  --blue-dark:#16406b;
  --navy:#0f2a47;
  --yellow:#f5b400;
  --text:#555a60;
  --heading:#1c2430;
  --light:#eef1f4;
  --slate:#3c5272;
  --footer:#1d1f22;
  --white:#ffffff;
}
*{margin:0;padding:0;box-sizing:border-box}
html,body{width:1200px;height:3636px;overflow:hidden}
body{font-family:'Lato',sans-serif;color:var(--text);background:var(--white);position:relative}
section,header,footer{position:absolute;left:0;width:1200px}
.btn{display:inline-block;background:var(--yellow);color:var(--white);font-size:13px;font-weight:700;letter-spacing:1px;padding:14px 30px;text-transform:uppercase}
.section-title{font-size:32px;font-weight:700;color:var(--heading);text-align:center}
.section-sub{font-size:14px;text-align:center;margin-top:14px}

/* header */
.site-header{top:0;height:80px;display:flex;align-items:center;justify-content:space-between;padding:0 60px;background:var(--white)}
.brand{font-size:30px;font-weight:400;color:var(--heading)}
.nav{display:flex;gap:28px;font-size:12px;font-weight:700;color:var(--heading)}
.nav a{padding-bottom:6px}
.nav .active{color:var(--blue);border-bottom:2px solid var(--blue)}

/* hero */
.hero{top:80px;height:640px;background:linear-gradient(110deg,#1b2330 0%,#3a4a5e 35%,#7d8a97 60%,#4b5563 100%)}
.hero-title{position:absolute;top:290px;width:100%;text-align:center;color:var(--white);font-size:66px;font-weight:700;line-height:1.05;text-shadow:0 2px 8px rgba(0,0,0,.35)}
.dots{position:absolute;left:0;width:100%;display:flex;justify-content:center;gap:10px}
.dots span{width:10px;height:10px;border-radius:50%;background:rgba(255,255,255,.55)}
.dots span.on{background:var(--white)}
.hero .dots{top:575px}

/* welcome */
.welcome{top:720px;height:340px;text-align:center;padding-top:50px}
.welcome p{width:900px;margin:26px auto 0;font-size:14px;line-height:26px}
.welcome .btn{margin-top:30px}

/* solutions */
.solutions{top:1060px;height:780px;background:var(--light)}
.solutions .section-title{position:absolute;top:80px;width:100%}
.ring{position:absolute;left:0;top:0}
.sol-item{position:absolute;width:260px;font-size:12px;line-height:18px}
.sol-item h3{font-size:17px;color:var(--blue);font-weight:700;margin-bottom:6px}
.sol-item.left{text-align:right}
.solutions .btn{position:absolute;top:680px;left:50%;transform:translateX(-50%)}

/* what we do */
.what{top:1840px;height:460px;background:var(--navy);color:#cfd8e3}
.what .section-title{color:var(--white);margin-top:56px}
.what .section-sub{color:#cfd8e3}
.cards{display:flex;gap:40px;justify-content:center;margin-top:40px}
.card{width:240px;height:250px;background:linear-gradient(180deg,#2476bd,#16508c);padding:22px 20px;text-align:center;box-shadow:0 6px 14px rgba(0,0,0,.35)}
.card h3{color:var(--yellow);font-size:17px;font-weight:700;margin-bottom:12px}
.card p{font-size:12px;line-height:18px;color:var(--white)}

/* testimonials */
.testimonials{top:2300px;height:480px;background:linear-gradient(135deg,#4a5f80,#34486a 55%,#2c3d5c);text-align:center;color:var(--white)}
.testimonials .section-title{color:var(--white);margin-top:60px}
.quote-mark{display:block;margin:26px auto 0}
.testimonials p{width:900px;margin:18px auto 0;font-size:14px;line-height:26px}
.testimonials .name{color:var(--yellow);font-size:13px;font-weight:700;margin-top:18px}
.testimonials .dots{top:384px}

/* blog */
.blog{top:2780px;height:500px;text-align:center}
.blog .section-title{margin-top:56px}
.posts{display:flex;gap:40px;justify-content:center;margin-top:36px}
.post{width:320px}
.post-img{position:relative;height:190px}
.date{position:absolute;left:20px;bottom:-14px;width:54px;height:64px;background:var(--yellow);color:var(--white);font-weight:700;text-align:center;padding-top:8px;font-size:11px;line-height:14px}
.date b{display:block;font-size:24px;line-height:28px}
.post h4{font-size:15px;color:var(--blue);font-weight:700;margin-top:34px;line-height:20px}
.post .more{display:block;font-size:12px;font-weight:700;color:var(--heading);margin-top:18px}

/* footer */
.site-footer{top:3280px;height:356px;background:var(--footer);color:#b9bcc0;display:flex;gap:0;padding:50px 80px 0}
.f-col{font-size:12px;line-height:22px}
.f-col h5{color:var(--white);font-size:13px;font-weight:700;margin-bottom:12px;letter-spacing:.5px}
.f-brand{width:260px}
.f-brand .brand{color:var(--white);font-size:28px;margin-bottom:12px}
.social{display:flex;gap:12px;margin-top:16px}
.social span{width:14px;height:14px;border-radius:50%;background:#b9bcc0}
.f-map{width:280px}
.f-map .cols{display:flex;gap:50px}
.f-contact{width:280px}
.f-signup{width:240px}
.signup{display:flex;margin-top:6px}
.signup span{width:150px;height:34px;background:var(--white);color:#888;padding:6px 10px;font-size:12px}
.signup b{background:var(--yellow);color:var(--white);font-size:11px;padding:8px 12px}
</style>
</head>
<body>

<header class="site-header">
  <div class="brand">QRH Software</div>
  <nav class="nav">
    <a class="active">HOME</a><a>ABOUT US</a><a>SERVICES</a><a>SOLUTION</a><a>CAREER WITH US</a><a>BLOG</a><a>CONTACT</a>
  </nav>
</header>

<section class="hero" role="img" aria-label="Photo of IT professionals working at computer screens in an office">
  <h1 class="hero-title">Technology Business<br>Management</h1>
  <div class="dots"><span></span><span class="on"></span><span></span><span></span></div>
</section>

<section class="welcome">
  <h2 class="section-title">Welcome to Our Website</h2>
  <p>Lorem ipsum dolor sit amet, consectetur adipisicing elit, sed do eiusmod tempor incididunt ut labore et dolore magna aliqua. Ut enim ad minim veniam, quis nostrud exercitation ullamco laboris nisi ut aliquip ex ea commodo consequat. Duis aute irure dolor in reprehenderit in voluptate velit esse cillum dolore eu fugiat nulla pariatur. Excepteur sint occaecat cupidatat non proident, sunt in culpa qui officia deserunt mollit anim id est laborum.</p>
  <span class="btn">Read More</span>
</section>

<section class="solutions">
  <h2 class="section-title">Our Solutions</h2>
  <svg class="ring" width="1200" height="780" viewBox="0 0 1200 780">
    <circle cx="600" cy="400" r="215" fill="#dfe8f1"/>
    <circle cx="600" cy="400" r="175" fill="none" stroke="#bcd3e8" stroke-width="3"/>
    <circle cx="600" cy="400" r="130" fill="#ffffff"/>
    <text x="600" y="390" text-anchor="middle" font-family="Lato,sans-serif" font-size="50" font-weight="700" fill="#1c2430">QRH</text>
    <text x="600" y="445" text-anchor="middle" font-family="Lato,sans-serif" font-size="50" font-weight="700" fill="#1c2430">Software</text>
    <g fill="#ffffff" stroke="#1f7fc4" stroke-width="3">
      <circle cx="513" cy="250" r="26"/><circle cx="427" cy="400" r="26"/><circle cx="513" cy="550" r="26"/>
    </g>
    <g fill="#1f7fc4">
      <circle cx="687" cy="250" r="26"/><circle cx="773" cy="400" r="26"/><circle cx="687" cy="550" r="26"/>
    </g>
    <g fill="#1f7fc4">
      <rect x="503" y="252" width="5" height="10"/><rect x="511" y="244" width="5" height="18"/><rect x="519" y="248" width="5" height="14"/>
    </g>
    <path d="M417 396a11 11 0 0 1 19-6M437 404a11 11 0 0 1-19 6" fill="none" stroke="#1f7fc4" stroke-width="3"/>
    <circle cx="510" cy="547" r="8" fill="none" stroke="#1f7fc4" stroke-width="3"/>
    <line x1="516" y1="553" x2="523" y2="560" stroke="#1f7fc4" stroke-width="3"/>
    <g fill="#ffffff">
      <circle cx="687" cy="243" r="6"/><rect x="677" y="252" width="20" height="9" rx="4"/>
      <text x="773" y="408" text-anchor="middle" font-family="Lato,sans-serif" font-size="22" font-weight="700">$</text>
      <path d="M679 550l6 6 10-12" fill="none" stroke="#ffffff" stroke-width="3"/>
    </g>
  </svg>
  <div class="sol-item left" style="left:220px;top:225px"><h3>Position for Value</h3>Define what you deliver in terms of business capabilities that are valued by your business.</div>
  <div class="sol-item left" style="left:135px;top:370px"><h3>Continuously Improve</h3>Execute a strategic roadmap for QRH maturity by reviewing results on a regular basis.</div>
  <div class="sol-item left" style="left:220px;top:520px"><h3>Create Transparency</h3>Translate cost, spending and capacity into clear views for business decision makers.</div>
  <div class="sol-item" style="left:720px;top:225px"><h3>Shape Business Demand</h3>Communicate costs and consumption so business units can make informed choices.</div>
  <div class="sol-item" style="left:805px;top:370px"><h3>Deliver Value for Money</h3>Maximize value and benchmark your cost effectiveness for services.</div>
  <div class="sol-item" style="left:720px;top:520px"><h3>Plan &amp; Govern</h3>Collaborate to align cost, budget and resources to strategic priorities.</div>
  <span class="btn">View All Solutions</span>
</section>

<section class="what">
  <h2 class="section-title">What We Do</h2>
  <p class="section-sub">Lorem ipsum dolor sit amet, consectetur adipisicing elit, sed do eiusmod tempor incididunt ut labore et dolore magna aliqua.</p>
  <div class="cards">
    <div class="card"><h3>IT Leaders</h3><p>"QRH brings business transparency to you and your people, so you can focus on the value you deliver, drive improvement and partner with the business."<br>Dana Holt, Global CTO, Norvane</p></div>
    <div class="card"><h3>CFOs</h3><p>"I changed the discussion with the CTO from 'We're only spending money' to 'We really are managing what we're doing'."<br>Paul Renner, Executive Director IT Finance, Halverd Health</p></div>
    <div class="card"><h3>CEOs</h3><p>"All of a sudden, we had clarity. That's the benefit of QRH. It has made a major difference to our company and how we run the business."<br>Lena Marsh, CEO, Crestline Financial Group</p></div>
    <div class="card"><h3>Business Unit Executives</h3><p>"IT has shifted from being an order taker to an originator of ideas to aid in the businesses."<br>Alan Ford, VP Information Technology, Petrovane</p></div>
  </div>
</section>

<section class="testimonials">
  <h2 class="section-title">Testimonials</h2>
  <svg class="quote-mark" width="40" height="30" viewBox="0 0 40 30" aria-hidden="true">
    <path d="M2 30V16C2 7 7 2 16 0v6c-5 2-7 5-7 10h7v14zM24 30V16c0-9 5-14 14-16v6c-5 2-7 5-7 10h7v14z" fill="#f5b400"/>
  </svg>
  <p>Lorem ipsum dolor sit amet, consectetur adipisicing elit, sed do eiusmod tempor incididunt ut labore et dolore magna aliqua. Ut enim ad minim veniam, quis nostrud exercitation ullamco laboris nisi ut aliquip ex ea commodo consequat. Duis aute irure dolor in reprehenderit in voluptate velit esse cillum dolore eu fugiat nulla pariatur.</p>
  <div class="name">Jordan Miles</div>
  <div class="dots"><span class="on"></span><span></span><span></span><span></span></div>
</section>

<section class="blog">
  <h2 class="section-title">Blog Posts</h2>
  <p class="section-sub">Lorem ipsum dolor sit amet, consectetur adipisicing elit, sed do eiusmod tempor incididunt ut labore et dolore magna aliqua.</p>
  <div class="posts">
    <div class="post">
      <div class="post-img" role="img" aria-label="Photo of a team working at a laptop" style="background:linear-gradient(135deg,#2f4c6e,#8a6a4a 60%,#c9b49a)"><div class="date">MAR<b>18</b></div></div>
      <h4>LOREM IPSUM DOLOR SIT AMET,<br>CONSECTETUR</h4><span class="more">READ MORE</span>
    </div>
    <div class="post">
      <div class="post-img" role="img" aria-label="Photo of a business meeting around a table" style="background:linear-gradient(135deg,#5b4a3a,#a08464 55%,#d8cbb8)"><div class="date">MAR<b>18</b></div></div>
      <h4>LOREM IPSUM DOLOR SIT AMET,<br>CONSECTETUR</h4><span class="more">READ MORE</span>
    </div>
    <div class="post">
      <div class="post-img" role="img" aria-label="Illustration of analytics charts on a screen" style="background:linear-gradient(135deg,#bfe3f5,#4fa6dc 60%,#2a78b8)"><div class="date">MAR<b>18</b></div></div>
      <h4>LOREM IPSUM DOLOR SIT AMET,<br>CONSECTETUR</h4><span class="more">READ MORE</span>
    </div>
  </div>
</section>

<footer class="site-footer">
  <div class="f-col f-brand">
    <div class="brand">QRH Software</div>
    Copyright © 2015 QRH Software.<br>All Rights Reserved.
    <div class="social"><span></span><span></span><span></span><span></span><span></span></div>
  </div>
  <div class="f-col f-map">
    <h5>SITE MAP</h5>
    <div class="cols"><div>Home<br>About Us<br>Services<br>Blog</div><div>Career With Us<br>Solution<br>Contact</div></div>
  </div>
  <div class="f-col f-contact">
    <h5>CONTACT INFO</h5>
    12 Harbor Lane, Westfield,<br>NY 10234<br>1-800-555-0176<br>info@qrhsoftware.com<br>Map Direction
  </div>
  <div class="f-col f-signup">
    <h5>EMAIL SIGN UP</h5>
    <div class="signup"><span>Enter Email Address</span></div>
    <div style="margin-top:10px"><span class="btn" style="padding:8px 16px;font-size:11px">Sign Up</span></div>
  </div>
</footer>

</body>
</html>
```